"Harbor Builders" is a residential building company and needs a new business card design and may re

We would like a redesign based on the existing logo, and would like to see a new font as well. We are bespoke home builders who build sustainable energy efficient homes.

Industry/Entity Type

Construction

Contact Information for Business Card

Business card size 40mm x 90mm

Colors

Designer to choose colors to be used in the design.

```html
<!DOCTYPE html>
<html lang="en">
<head>
<meta charset="utf-8">
<title>Harbor Builders – Business Card</title>
<link href="https://fonts.googleapis.com/css2?family=Roboto:wght@400;500;700&family=Roboto+Condensed:wght@700&display=swap" rel="stylesheet">
<style>
  :root {
    --backdrop: #5b4a3a;
    --card-white: #f1f1f1;
    --card-black: #060708;
    --ink: #0b0b0b;
    --text-grey: #474747;
    --lime: #b2cb2b;
    --white: #ffffff;
  }
  * { margin: 0; padding: 0; box-sizing: border-box; }
  html, body {
    width: 1200px; height: 960px; overflow: hidden;
    background: var(--backdrop);
    font-family: "Roboto", Arial, sans-serif;
  }
  .card {
    position: absolute;
    width: 600px; height: 342px;
    box-shadow: 2px 3px 5px rgba(0,0,0,0.45);
    overflow: hidden;
  }
  .card-front { left: 314px; top: 113px; background: var(--card-white); }
  .card-back { left: 311px; top: 472px; background: var(--card-black); }

  .brand {
    position: absolute; display: flex; align-items: center; gap: 14px;
  }
  .brand-mark { background: var(--lime); }
  .card-front .brand { left: 41px; top: 52px; }
  .card-front .brand-mark { width: 24px; height: 24px; }
  .card-front .brand-name { font-size: 30px; font-weight: 500; color: var(--ink); letter-spacing: -0.3px; }

  .details {
    position: absolute; left: 40px; top: 155px;
    font-size: 14.5px; line-height: 18.5px; color: var(--text-grey);
  }
  .company { font-weight: 700; }
  .legal { margin-top: 3px; }
  .contacts { list-style: none; margin-top: 4px; }
  .contacts li { display: flex; align-items: center; gap: 8px; height: 19.5px; }
  .contacts svg { width: 14px; height: 14px; fill: var(--ink); flex: none; }

  .person-name {
    position: absolute; right: 41px; top: 221px;
    font-family: "Roboto Condensed", Arial, sans-serif;
    font-weight: 700; font-size: 23px; color: var(--ink); letter-spacing: -0.2px;
  }
  .edge-chevron { position: absolute; right: 0; top: 208px; width: 24px; height: 52px; }

  .card-back .brand { left: 0; right: 0; top: 138px; justify-content: center; gap: 22px; }
  .card-back .brand-mark { width: 44px; height: 44px; }
  .card-back .brand-name { font-size: 52px; font-weight: 500; color: var(--white); }
  .back-url {
    position: absolute; left: 0; right: 0; top: 296px; text-align: center;
    font-size: 14.5px; letter-spacing: 3.2px; color: var(--white);
  }
</style>
</head>
<body>
  <section class="card card-front">
    <div class="brand">
      <span class="brand-mark"></span>
      <span class="brand-name">Harbor Builders</span>
    </div>

    <div class="details">
      <p class="company">Harbor Builders Pty Ltd</p>
      <p>PO Box 7720 Lakeside</p>
      <p>LPO Kelmscott WA 6111</p>
      <p class="legal">Registration 48391</p>
      <p>ABN: 42 305 618 774</p>
      <ul class="contacts">
        <li>
          <svg viewBox="0 0 14 14"><path d="M4 0h6a1 1 0 0 1 1 1v12a1 1 0 0 1-1 1H4a1 1 0 0 1-1-1V1a1 1 0 0 1 1-1zm0.6 1.8v9h4.8v-9z"/></svg>
          0400 123 987
        </li>
        <li>
          <svg viewBox="0 0 14 14"><path d="M1 3h12v1.2L7 8 1 4.2z"/><path d="M1 5.6 7 9.4l6-3.8V11H1z"/></svg>
          daniel@harborbuilders.com.au
        </li>
        <li>
          <svg viewBox="0 0 14 14"><circle cx="7" cy="7" r="6.3"/><path d="M4 3.5c1.5.3 2 1.3 1.4 2.3-.6.9.4 1.6 1.3 1.7.8.1.7 1.5 0 2.4M8.5 1.6c-.2 1 .6 1.7 1.6 1.6 1 0 1.7.8 1.6 1.8" stroke="#f1f1f1" stroke-width="1.2" fill="none"/></svg>
          www.harborbuilders.com.au
        </li>
      </ul>
    </div>

    <p class="person-name">DANIEL MORETTI</p>
    <svg class="edge-chevron" viewBox="0 0 24 52">
      <polygon points="24,0 24,4 2,26 24,48 24,52 0,26" fill="var(--lime)"/>
      <polygon points="24,10 8,26 24,42" fill="var(--ink)"/>
    </svg>
  </section>

  <section class="card card-back">
    <div class="brand">
      <span class="brand-mark"></span>
      <span class="brand-name">Harbor Builders</span>
    </div>
    <p class="back-url">www.harborbuilders.com.au</p>
  </section>
</body>
</html>
```